Brindle Asset Management Vendor Recruiting Email

We need a digital flyer to email and post on Social media to attract new vendors to our website to apply to complete maintenance work on our clients homes. I have one flyer we had produced recently that we are un-happy with. It is attached.

The example given is what we do not want!! We do not want any of the pictures used from the existing one

Target Market(s)

Construction companies and handyman

Industry/Entity Type

Residential maintenance and repairs

Requirements
Must have
• Join our team as the header not become a vendor

```html
<!DOCTYPE html>
<html lang="en">
<head>
<meta charset="utf-8">
<title>Join Our Team – Brindle Asset Management</title>
<link href="https://fonts.googleapis.com/css2?family=Yellowtail&family=Montserrat:ital,wght@0,500;0,600;0,900;1,600&family=Oswald:wght@600;700&display=swap" rel="stylesheet">
<style>
  :root{
    --purple:#664d7e;
    --lime:#d4dd1f;
    --white:#ffffff;
    --ink:#050307;
    --logo-bg:#0d0b1a;
    --blue:#1b75bb;
    --lavender:#8a88c4;
    --tag-purple:#5b2a8c;
    --page:#ffffff;
  }
  *{margin:0;padding:0;box-sizing:border-box}
  html,body{width:1200px;height:1200px;overflow:hidden;background:var(--page)}
  .flyer{position:absolute;left:30px;top:90px;width:1140px;height:1020px;background:var(--purple);font-family:"Montserrat",sans-serif;color:var(--white)}
  .frame{position:absolute;left:32px;top:18px;width:1077px;height:983px;border:2px solid var(--white);border-radius:24px;overflow:hidden}
  .footer-band{position:absolute;left:0;right:0;top:902px;height:60px;background:var(--ink)}
  .footer-strip{position:absolute;left:0;right:0;top:962px;bottom:0;background:var(--lavender)}
  .headline-script{position:absolute;left:0;width:100%;top:52px;text-align:center;font-family:"Yellowtail",cursive;font-size:104px;line-height:1;color:var(--white);text-shadow:2px 3px 4px rgba(0,0,0,.35)}
  .headline-today{position:absolute;left:0;width:100%;top:148px;text-align:center;font-family:"Montserrat",sans-serif;font-weight:900;font-size:118px;letter-spacing:-2px;line-height:1;color:var(--lime);text-shadow:3px 4px 5px rgba(0,0,0,.35)}
  .benefits,.requirements ul{list-style:none}
  .benefits{position:absolute;left:62px;top:312px;width:450px}
  .benefits li{position:relative;padding-left:25px;font-size:24px;font-weight:600;line-height:33px;margin-bottom:32px}
  .benefits li:nth-child(2){margin-bottom:34px}
  .benefits li::before,.requirements li::before{content:"";position:absolute;left:0;top:10px;width:11px;height:11px;border-radius:50%;background:var(--lime)}
  .divider{position:absolute;left:553px;top:292px;width:2px;height:435px;background:var(--white)}
  .requirements{position:absolute;left:582px;top:290px;width:520px}
  .requirements h2{font-family:"Oswald",sans-serif;font-weight:600;font-size:39px;line-height:48px;color:var(--lime);margin-bottom:10px;text-transform:uppercase}
  .requirements li{position:relative;padding-left:34px;font-size:21.5px;font-weight:600;line-height:28px;margin-bottom:24px}
  .requirements li::before{left:8px;top:9px}
  .requirements li:nth-child(3){margin-bottom:24px}
  .contact-tag{position:absolute;left:228px;top:742px;width:143px;height:46px;background:var(--white);border-radius:4px;transform:rotate(-3deg);text-align:center;font-family:"Oswald",sans-serif;font-weight:700;font-size:25px;line-height:46px;color:var(--tag-purple);box-shadow:2px 2px 4px rgba(0,0,0,.3)}
  .phone-box{position:absolute;left:153px;top:772px;width:484px;height:118px;background:var(--blue);border:3px solid var(--white);border-radius:8px;transform:rotate(-3deg);text-align:center;font-family:"Oswald",sans-serif;font-weight:700;font-size:80px;line-height:110px;color:var(--white);box-shadow:3px 4px 6px rgba(0,0,0,.35)}
  .website{position:absolute;left:160px;top:940px;display:flex;align-items:center;gap:8px;font-style:italic;font-weight:600;font-size:24px;color:var(--white)}
  .brand-box{position:absolute;left:750px;top:832px;width:262px;height:148px;background:var(--logo-bg);display:flex;flex-direction:column;align-items:center;justify-content:center;gap:10px}
  .brand-mark{width:18px;height:18px;background:var(--white)}
  .brand-name{font-weight:600;font-size:17px;line-height:22px;color:var(--white);text-align:center;letter-spacing:1px;text-transform:uppercase}
</style>
</head>
<body>
<article class="flyer">
  <div class="frame">
    <div class="footer-band"></div>
    <div class="footer-strip"></div>
  </div>

  <h1 class="headline-script">Join Our Team</h1>
  <p class="headline-today">TODAY!</p>

  <ul class="benefits">
    <li>95% approval rating on all submitted estimates.</li>
    <li>Guaranteed work volume.</li>
    <li>Material purchasing program to help vendors with low capital or no or bad credit.</li>
    <li>Weekly secure direct deposit with net 30 payment terms.</li>
  </ul>

  <div class="divider"></div>

  <section class="requirements">
    <h2>Requirements to become a vendor</h2>
    <ul>
      <li>Auto insurance</li>
      <li>Certificate of general liability insurance</li>
      <li>Workman’s Compensation or state issued exemption letter</li>
      <li>Drive License or state issued ID card</li>
      <li>Coverage area</li>
      <li>Any speciality Licenses</li>
    </ul>
  </section>

  <div class="contact-tag">CONTACT</div>
  <div class="phone-box">615-555-0142</div>

  <div class="website">
    <svg width="28" height="28" viewBox="0 0 28 28" fill="none" stroke="#fff" stroke-width="2" aria-hidden="true">
      <circle cx="14" cy="14" r="12"/><ellipse cx="14" cy="14" rx="5" ry="12"/><line x1="2" y1="14" x2="26" y2="14"/>
    </svg>
    <span>www.brindleassetmanagement.com</span>
  </div>

  <div class="brand-box">
    <span class="brand-mark"></span>
    <span class="brand-name">Brindle<br>Asset Management</span>
  </div>
</article>
</body>
</html>
```